Kestrel Facilities Business Card Design

We would now like to design business cards with the new Kestrel Facilities logo

Target Market(s)

Professional

Industry/Entity Type

Professional services

Contact Information for Business Card

Employee name, title, phone number, email address, corporate office address and logo.

Font styles to use
Sans Serif

Colors
0054AA
0677BA
7BADD7
CADEEF
E8F1F8

Requirements
Must have
• My logo
Should not have
• any other pictures or images besides my logo

```html
<!DOCTYPE html>
<html lang="en">
<head>
<meta charset="utf-8">
<title>Kestrel Facilities – Business Card</title>
<link href="https://fonts.googleapis.com/css2?family=Figtree:wght@400;600;800&display=swap" rel="stylesheet">
<style>
  :root {
    --brand-blue: #3777bd;
    --ink: #1a1a1a;
    --paper: #ffffff;
    --backdrop: #e9eaec;
  }
  html, body {
    margin: 0;
    padding: 0;
    width: 1160px;
    height: 1200px;
    overflow: hidden;
    background: var(--backdrop);
    font-family: "Figtree", Arial, sans-serif;
  }
  .card {
    position: absolute;
    left: 191px;
    width: 778px;
    height: 441px;
    background: var(--paper);
    overflow: hidden;
  }
  .card--front { top: 105px; }
  .card--back  { top: 634px; }

  .header-band {
    position: absolute;
    left: 0; top: 0;
    width: 778px;
    height: 150px;
    background: var(--brand-blue);
  }
  .holder {
    position: absolute;
    left: 27px;
    top: 44px;
    color: var(--paper);
  }
  .holder__name {
    margin: 0;
    font-weight: 800;
    font-size: 29px;
    letter-spacing: -0.2px;
    line-height: 1;
  }
  .holder__title {
    margin: 8px 0 0;
    font-weight: 400;
    font-size: 21px;
    line-height: 1;
  }
  .address {
    position: absolute;
    left: 28px;
    top: 238px;
    margin: 0;
    font-style: normal;
    font-size: 20px;
    line-height: 29px;
    color: var(--ink);
  }
  .contacts {
    position: absolute;
    left: 26px;
    top: 318px;
    margin: 0;
    padding: 0;
    list-style: none;
    font-size: 20px;
    color: var(--ink);
  }
  .contacts li {
    display: flex;
    align-items: center;
    height: 30px;
  }
  .contacts svg {
    width: 19px;
    height: 19px;
    margin-right: 7px;
    flex: none;
  }
  .brand {
    position: absolute;
    display: flex;
    align-items: center;
    color: var(--brand-blue);
    font-weight: 600;
    line-height: 1.05;
  }
  .brand__square {
    background: var(--brand-blue);
    flex: none;
  }
  .brand--front {
    left: 438px;
    top: 246px;
    font-size: 46px;
  }
  .brand--front .brand__square {
    width: 60px; height: 60px; margin-right: 20px;
  }
  .brand--back {
    left: 0; right: 0;
    top: 162px;
    justify-content: center;
    font-size: 56px;
  }
  .brand--back .brand__square {
    width: 72px; height: 72px; margin-right: 24px;
  }
</style>
</head>
<body>

<section class="card card--front">
  <div class="header-band" role="img" aria-label="Blue header band with decorative wave"></div>

  <header class="holder">
    <h1 class="holder__name">DANA WHITFIELD</h1>
    <p class="holder__title">Co-Founder</p>
  </header>

  <address class="address">1840 Harbor View Drive<br>Suite 204 Lakemont 47</address>

  <ul class="contacts">
    <li>
      <svg viewBox="0 0 20 20" aria-hidden="true"><path fill="var(--brand-blue)" d="M2 7c0-3 4-4 8-4s8 1 8 4v2h-4V7H6v2H2z M5 10h10l2 7H3z"/></svg>
      +254-700-41523
    </li>
    <li>
      <svg viewBox="0 0 20 20" aria-hidden="true"><rect x="1" y="4" width="18" height="12" fill="var(--brand-blue)"/><path d="M1 5l9 7 9-7" fill="none" stroke="#fff" stroke-width="1.6"/></svg>
      info@kestrelfacilities.com
    </li>
    <li>
      <svg viewBox="0 0 20 20" aria-hidden="true"><circle cx="10" cy="10" r="9" fill="var(--brand-blue)"/><path d="M1 10h18M10 1c-4 4-4 14 0 18M10 1c4 4 4 14 0 18" fill="none" stroke="#fff" stroke-width="1.3"/></svg>
      www.kestrelfacilities.com
    </li>
  </ul>

  <div class="brand brand--front">
    <span class="brand__square"></span>
    <span class="brand__name">Kestrel<br>Facilities</span>
  </div>
</section>

<section class="card card--back">
  <div class="brand brand--back">
    <span class="brand__square"></span>
    <span class="brand__name">Kestrel<br>Facilities</span>
  </div>
</section>

</body>
</html>
```